Business Card Design Project

Business Card design based on logo.
Updates

I need business card, letterhead, envelope, and if possible, Powerpoint slide template.

On front of business card: Just logo- and  my name and title:  Harriet Lindqvist, Principal

On reverse-logo and the rest of the contact info:

4871 Quarry Lane
Davis, CA 95618
650-318-2764
hl@brackenstudyworks.example

On letterhead-Just logo at top, at bottom  the rest-very small along the bottom

On PPT slide-just the logo.

I also want to try a few other colors-I like lime/dark grey (not black) but would like to try Sienna, maybe also indigo or bright blue-green.

I forgot to add-

On the business card-switch to vertical on reverse side and put:

Reverse side-switch to vertical and list:

Harriet Lindqvist
Principal
Bracken Study Works, LLC

650-318-2764

4871 Quarry Lane
Davis, CA 95618

Harriet Lindqvist
Principal

650-318-2764

4871 Quarry Lane
Davis, CA 95618

I have another project at the same time-for Stationery. Feel free to submit to that one also.

That one includes letterhead, envelope, PPT slide, folder cover sheet-HL

Industry/Entity Type

Business

Requirements
Must have
• Must use logo-preferably lime green version-with gray, not black or just 2-tone -logo on colored background.

```html
<!DOCTYPE html>
<html lang="en">
<head>
<meta charset="utf-8">
<title>Bracken Study Works – Business Cards</title>
<link rel="stylesheet" href="https://fonts.googleapis.com/css2?family=Gilda+Display&family=Questrial&family=Libre+Baskerville:wght@400;700&display=swap">
<style>
  :root {
    --lime: #96b83f;
    --grey: #4a4a4c;
    --rule: #8a8a8a;
    --paper: #ffffff;
    --backdrop: #6e3b2b;
    --wordmark: "Gilda Display", serif;
    --sans: "Questrial", sans-serif;
    --serif: "Libre Baskerville", serif;
  }
  * { box-sizing: border-box; margin: 0; padding: 0; }
  html, body { width: 1200px; height: 704px; overflow: hidden; }
  body { background: var(--backdrop); position: relative; font-family: var(--sans); }

  .card {
    position: absolute;
    width: 501px;
    height: 287px;
    background: var(--paper);
    border-radius: 16px;
    overflow: hidden;
  }
  .card--contact { left: 84px; top: 43px; }
  .card--green   { left: 622px; top: 55px; background: var(--lime); border-radius: 24px; }
  .card--large   { left: 89px; top: 369px; }
  .card--logo    { left: 622px; top: 373px; border-radius: 22px; }

  .wordmark {
    position: absolute;
    left: 0; right: 0;
    text-align: center;
    font-family: var(--wordmark);
    font-weight: 400;
    color: var(--grey);
    line-height: 1;
  }
  .wordmark__line { display: block; }
  .mark-square {
    position: absolute;
    left: 50%;
    background: var(--lime);
    transform: translateX(-50%);
  }

  /* contact card */
  .card--contact .mark-square { top: 20px; width: 26px; height: 26px; }
  .card--contact .wordmark { top: 60px; font-size: 36px; letter-spacing: 6px; }
  .card--contact .wordmark .wordmark__line + .wordmark__line { font-size: 19px; letter-spacing: 6px; margin-top: 5px; }
  .rule { position: absolute; left: 0; right: 0; height: 2px; background: var(--rule); }
  .rule--top { top: 148px; }
  .rule--bottom { top: 253px; }
  .contact-band {
    position: absolute; left: 0; right: 0; top: 152px; height: 99px;
    background: var(--lime);
    color: var(--paper);
    font-family: var(--serif);
    font-size: 12.5px;
  }
  .address {
    position: absolute; right: 290px; top: 29px;
    text-align: right; line-height: 20px;
  }
  .band-divider { position: absolute; left: 222px; top: 18px; width: 1.5px; height: 62px; background: var(--paper); }
  .contact-list { position: absolute; left: 236px; top: 20px; list-style: none; line-height: 20px; }
  .contact-list li { display: flex; align-items: center; gap: 6px; white-space: nowrap; }
  .contact-list svg { width: 10px; height: 10px; fill: var(--paper); flex: none; }
  .signature {
    position: absolute; left: 0; right: 0; top: 259px;
    text-align: center; font-family: var(--serif); color: var(--grey); font-size: 12px;
  }
  .signature__name { color: var(--lime); font-weight: 700; font-size: 16px; }

  .web {
    position: absolute; left: 0; right: 0; top: 249px;
    text-align: center; font-family: var(--sans); font-size: 19px; letter-spacing: 3px; color: var(--grey);
  }

  /* green card */
  .card--green .wordmark { top: 86px; color: var(--paper); font-size: 50px; letter-spacing: 8px; }
  .card--green .wordmark .wordmark__line + .wordmark__line { font-size: 24px; letter-spacing: 9px; margin-top: 10px; }
  .card--green .web { color: var(--paper); top: 246px; }

  /* large wordmark card */
  .card--large .wordmark { top: 82px; font-size: 62px; letter-spacing: 10px; }
  .card--large .wordmark .wordmark__line + .wordmark__line { font-size: 30px; letter-spacing: 10px; margin-top: 12px; }

  /* logo card */
  .card--logo .mark-square { top: 52px; width: 40px; height: 40px; }
  .card--logo .wordmark { top: 124px; font-size: 42px; letter-spacing: 7px; }
  .card--logo .wordmark .wordmark__line + .wordmark__line { font-size: 21px; letter-spacing: 7px; margin-top: 8px; }
</style>
</head>
<body>

<section class="card card--contact">
  <div class="mark-square"></div>
  <h1 class="wordmark"><span class="wordmark__line">BRACKEN</span><span class="wordmark__line">STUDY WORKS</span></h1>
  <div class="rule rule--top"></div>
  <div class="contact-band">
    <p class="address">4871 Quarry Lane<br>Davis, CA 95618</p>
    <div class="band-divider"></div>
    <ul class="contact-list">
      <li><svg viewBox="0 0 10 10"><path d="M2 0.5 L3.8 2.6 L2.9 3.6 Q4 6 6.4 7.1 L7.4 6.2 L9.5 8 L8.2 9.5 Q2.5 8.6 0.5 1.8 Z"/></svg>650-318-2764</li>
      <li><svg viewBox="0 0 10 10"><path d="M0.5 2 H9.5 V8.5 H0.5 Z M1.2 2.6 L5 5.6 L8.8 2.6" stroke="#96b83f" stroke-width="0.8"/></svg>hl@brackenstudyworks.example</li>
      <li><svg viewBox="0 0 10 10"><circle cx="5" cy="5" r="4.5"/><path d="M0.5 5 H9.5 M5 0.5 V9.5" stroke="#96b83f" stroke-width="0.8"/></svg>www.brackenstudyworks.example</li>
    </ul>
  </div>
  <div class="rule rule--bottom"></div>
  <p class="signature"><span class="signature__name">Harriet Lindqvist,</span> Principal</p>
</section>

<section class="card card--green">
  <h2 class="wordmark"><span class="wordmark__line">BRACKEN</span><span class="wordmark__line">STUDY WORKS</span></h2>
  <p class="web">www.brackenstudyworks.example</p>
</section>

<section class="card card--large">
  <h2 class="wordmark"><span class="wordmark__line">BRACKEN</span><span class="wordmark__line">STUDY WORKS</span></h2>
  <p class="web">www.brackenstudyworks.example</p>
</section>

<section class="card card--logo">
  <div class="mark-square"></div>
  <h2 class="wordmark"><span class="wordmark__line">BRACKEN</span><span class="wordmark__line">STUDY WORKS</span></h2>
  <p class="web">www.brackenstudyworks.example</p>
</section>

</body>
</html>
```